Dental Medical History Form - Content provided

Design a medical history form for a dental practice. Content is provided so all that is needed is the formatting to make it look great and easy to read.

"Patient Information" to include all information contained in top portion of the "Patient Medical History Form" docx file.

"Medical History" should follow the formatting and content of the "Exact Medical History" file as this is what the entry fields look like in our practice software and so we would like it to match.

1st page - Patient info, allergies, medications, antibiotics, joint replacement, pregnancy.

2nd page - Do you have, or have you had, any of the following? . . . . . . .
Updates

Target Market(s)

All ages but must be clear enough for elderly to read. Use as much space as possible to keep font size bigger yet keep to two pages

Industry/Entity Type

Dental

Font styles to use
Sans Serif

Requirements
Must have
• All content provided
• Our logo at the top (file provided)
• Century Gothic Font
• Limit to two pages

```html
<!DOCTYPE html>
<html lang="en">
<head>
<meta charset="utf-8">
<title>Medical History Form – Page 2</title>
<link rel="stylesheet" href="https://fonts.googleapis.com/css2?family=Didact+Gothic&family=Montserrat:wght@600;700&display=swap">
<style>
  :root{
    --frame:#836a5a;
    --paper:#fdeee5;
    --ink:#3a3330;
    --box-line:#c9c2bd;
    --box-fill:#ffffff;
    --rule:#e6d6cc;
  }
  *{box-sizing:border-box;margin:0;padding:0}
  html,body{width:849px;height:1200px;overflow:hidden;background:var(--frame)}
  .page{position:absolute;left:14px;top:14px;width:821px;height:1173px;background:var(--paper);
        font-family:"Didact Gothic",sans-serif;color:var(--ink);font-size:13px}
  .abs{position:absolute}
  .page-title{left:50px;top:68px;font-family:"Montserrat",sans-serif;font-weight:700;font-size:12px}
  .section-head{font-family:"Montserrat",sans-serif;font-weight:700;font-size:12px;height:18px;line-height:18px}
  .column-rule{left:429px;top:109px;width:1px;height:991px;background:var(--rule)}
  .row{display:flex;align-items:center;height:19.8px;white-space:nowrap}
  .box{display:inline-block;width:21px;height:17px;background:var(--box-fill);border:1px solid var(--box-line);border-radius:2px}
  /* left column */
  .left{left:50px;width:345px}
  .left .label{width:239px}
  .left .yes{width:44px;padding-left:6px}
  .left .no{padding-left:7px}
  .row-tall{height:36px;align-items:flex-end;padding-bottom:1px}
  .row-tall .label{line-height:16px;white-space:normal;padding-bottom:0}
  /* right column */
  .right{left:458px;width:330px}
  .right .label{width:213px}
  .right .yes-word{width:24px}
  .right .no-word{width:21px;margin-left:13px}
  .closing{left:50px;width:360px;font-family:"Montserrat",sans-serif;font-weight:700;font-size:12.5px;line-height:19px}
  .field{border:1px solid var(--box-line);background:var(--box-fill)}
  .field-label{font-family:"Montserrat",sans-serif;font-weight:700;font-size:12.5px;padding:8px 6px}
</style>
</head>
<body>
<main class="page">
  <h1 class="abs page-title">Do you have, or have you had, any of the following ?</h1>
  <div class="abs column-rule"></div>

  <!-- LEFT COLUMN -->
  <section class="abs left" style="top:93px">
    <h2 class="section-head">DENTAL</h2>
    <div class="row"><span class="label">Acid Reflux</span><span class="box"></span><span class="yes">Yes</span><span class="box"></span><span class="no">No</span></div>
    <div class="row"><span class="label">Bad Breath/Taste</span><span class="box"></span><span class="yes">Yes</span><span class="box"></span><span class="no">No</span></div>
    <div class="row"><span class="label">Bleeding/Swollen/Sore Gums</span><span class="box"></span><span class="yes">Yes</span><span class="box"></span><span class="no">No</span></div>
    <div class="row"><span class="label">Blisters/Ulcers in Mouth</span><span class="box"></span><span class="yes">Yes</span><span class="box"></span><span class="no">No</span></div>
    <div class="row"><span class="label">Broken tooth/filling</span><span class="box"></span><span class="yes">Yes</span><span class="box"></span><span class="no">No</span></div>
    <div class="row"><span class="label">Burning tongue</span><span class="box"></span><span class="yes">Yes</span><span class="box"></span><span class="no">No</span></div>
    <div class="row"><span class="label">Dry mouth</span><span class="box"></span><span class="yes">Yes</span><span class="box"></span><span class="no">No</span></div>
    <div class="row"><span class="label">Food collection between teeth</span><span class="box"></span><span class="yes">Yes</span><span class="box"></span><span class="no">No</span></div>
    <div class="row"><span class="label">Grinding/clenching teeth (day/night)</span><span class="box"></span><span class="yes">Yes</span><span class="box"></span><span class="no">No</span></div>
    <div class="row"><span class="label">Loose teeth</span><span class="box"></span><span class="yes">Yes</span><span class="box"></span><span class="no">No</span></div>
    <div class="row"><span class="label">Crooked teeth</span><span class="box"></span><span class="yes">Yes</span><span class="box"></span><span class="no">No</span></div>
    <div class="row"><span class="label">Discoloured teeth</span><span class="box"></span><span class="yes">Yes</span><span class="box"></span><span class="no">No</span></div>
    <div class="row"><span class="label">Sensitivity to Hot/Cold</span><span class="box"></span><span class="yes">Yes</span><span class="box"></span><span class="no">No</span></div>
    <div class="row"><span class="label">Tooth pain when chewing</span><span class="box"></span><span class="yes">Yes</span><span class="box"></span><span class="no">No</span></div>
    <div class="row"><span class="label">Jaw pain/Fracture</span><span class="box"></span><span class="yes">Yes</span><span class="box"></span><span class="no">No</span></div>
    <div class="row"><span class="label">Orthodontic treatment/history</span><span class="box"></span><span class="yes">Yes</span><span class="box"></span><span class="no">No</span></div>
    <div class="row"><span class="label">Oral Cancer</span><span class="box"></span><span class="yes">Yes</span><span class="box"></span><span class="no">No</span></div>
  </section>

  <section class="abs left" style="top:468px">
    <h2 class="section-head">DIET/LIFESTYLE</h2>
    <div class="row row-tall"><span class="label">Drink more than 1glass<br>alcohol per day</span><span class="box"></span><span class="yes">Yes</span><span class="box"></span><span class="no">No</span></div>
    <div class="row"><span class="label">Smoking</span><span class="box"></span><span class="yes">Yes</span><span class="box"></span><span class="no">No</span></div>
    <div class="row"><span class="label">Carbonated drinks</span><span class="box"></span><span class="yes">Yes</span><span class="box"></span><span class="no">No</span></div>
    <div class="row"><span class="label">Sugary foods</span><span class="box"></span><span class="yes">Yes</span><span class="box"></span><span class="no">No</span></div>
  </section>

  <section class="abs left" style="top:602px">
    <h2 class="section-head">BLOOD</h2>
    <div class="row"><span class="label">Anaemia</span><span class="box"></span><span class="yes">Yes</span><span class="box"></span><span class="no">No</span></div>
    <div class="row"><span class="label">Blood clots</span><span class="box"></span><span class="yes">Yes</span><span class="box"></span><span class="no">No</span></div>
    <div class="row"><span class="label">Leukemia</span><span class="box"></span><span class="yes">Yes</span><span class="box"></span><span class="no">No</span></div>
    <div class="row"><span class="label">Low platelets</span><span class="box"></span><span class="yes">Yes</span><span class="box"></span><span class="no">No</span></div>
    <div class="row"><span class="label">Lymphoma</span><span class="box"></span><span class="yes">Yes</span><span class="box"></span><span class="no">No</span></div>
  </section>

  <section class="abs left" style="top:741px">
    <h2 class="section-head">CHEST</h2>
    <div class="row"><span class="label">Bronchitis</span><span class="box"></span><span class="yes">Yes</span><span class="box"></span><span class="no">No</span></div>
    <div class="row"><span class="label">Cystic Fibrosis</span><span class="box"></span><span class="yes">Yes</span><span class="box"></span><span class="no">No</span></div>
    <div class="row"><span class="label">Emphysema</span><span class="box"></span><span class="yes">Yes</span><span class="box"></span><span class="no">No</span></div>
    <div class="row"><span class="label">Pneumonia</span><span class="box"></span><span class="yes">Yes</span><span class="box"></span><span class="no">No</span></div>
  </section>

  <section class="abs left" style="top:860px">
    <h2 class="section-head">INFECTIOUS DISEASE</h2>
    <div class="row"><span class="label">Creutzfeldt-Jakob Disease</span><span class="box"></span><span class="yes">Yes</span><span class="box"></span><span class="no">No</span></div>
    <div class="row"><span class="label">Hepatitis A,B,C,D</span><span class="box"></span><span class="yes">Yes</span><span class="box"></span><span class="no">No</span></div>
    <div class="row"><span class="label">HIV/AIDS</span><span class="box"></span><span class="yes">Yes</span><span class="box"></span><span class="no">No</span></div>
  </section>

  <div class="abs closing" style="top:984px">
    <p>Thank you for the time to complete<br>your medical history form.</p>
    <p style="margin-top:21px">Oral health is linked to overall health and<br>this comprehensive questionnaire will help us to<br>provide you with optimal and safe care.</p>
  </div>

  <!-- RIGHT COLUMN -->
  <section class="abs right" style="top:110px">
    <div class="row"><span class="label">Influenza</span><span class="yes-word">Yes</span><span class="box"></span><span class="no-word">No</span><span class="box"></span></div>
    <div class="row"><span class="label">Shingles</span><span class="yes-word">Yes</span><span class="box"></span><span class="no-word">No</span><span class="box"></span></div>
    <div class="row"><span class="label">Tuberculosis</span><span class="yes-word">Yes</span><span class="box"></span><span class="no-word">No</span><span class="box"></span></div>
  </section>

  <section class="abs right" style="top:192px">
    <h2 class="section-head">HEART</h2>
    <div class="row"><span class="label">Angina</span><span class="yes-word">Yes</span><span class="box"></span><span class="no-word">No</span><span class="box"></span></div>
    <div class="row"><span class="label">Atrial Fibrillation</span><span class="yes-word">Yes</span><span class="box"></span><span class="no-word">No</span><span class="box"></span></div>
    <div class="row"><span class="label">Blood Pressure (High/Low)</span><span class="yes-word">Yes</span><span class="box"></span><span class="no-word">No</span><span class="box"></span></div>
    <div class="row"><span class="label">Congenital Heart Disease</span><span class="yes-word">Yes</span><span class="box"></span><span class="no-word">No</span><span class="box"></span></div>
    <div class="row"><span class="label">Heart attack</span><span class="yes-word">Yes</span><span class="box"></span><span class="no-word">No</span><span class="box"></span></div>
    <div class="row"><span class="label">Heart murmur</span><span class="yes-word">Yes</span><span class="box"></span><span class="no-word">No</span><span class="box"></span></div>
    <div class="row"><span class="label">Heart surgery</span><span class="yes-word">Yes</span><span class="box"></span><span class="no-word">No</span><span class="box"></span></div>
    <div class="row"><span class="label">Heart valve replacement</span><span class="yes-word">Yes</span><span class="box"></span><span class="no-word">No</span><span class="box"></span></div>
    <div class="row"><span class="label">Infective endocarditis</span><span class="yes-word">Yes</span><span class="box"></span><span class="no-word">No</span><span class="box"></span></div>
    <div class="row"><span class="label">Rheumatic Heart Disease</span><span class="yes-word">Yes</span><span class="box"></span><span class="no-word">No</span><span class="box"></span></div>
    <div class="row"><span class="label">Pacemaker</span><span class="yes-word">Yes</span><span class="box"></span><span class="no-word">No</span><span class="box"></span></div>
    <div class="row"><span class="label">Stent</span><span class="yes-word">Yes</span><span class="box"></span><span class="no-word">No</span><span class="box"></span></div>
  </section>

  <section class="abs right" style="top:470px">
    <h2 class="section-head">OTHER</h2>
    <div class="row"><span class="label">Anxiety/PTSD</span><span class="yes-word">Yes</span><span class="box"></span><span class="no-word">No</span><span class="box"></span></div>
    <div class="row"><span class="label">Arthritis</span><span class="yes-word">Yes</span><span class="box"></span><span class="no-word">No</span><span class="box"></span></div>
    <div class="row"><span class="label">Alzheimer's</span><span class="yes-word">Yes</span><span class="box"></span><span class="no-word">No</span><span class="box"></span></div>
    <div class="row"><span class="label">Asthma</span><span class="yes-word">Yes</span><span class="box"></span><span class="no-word">No</span><span class="box"></span></div>
    <div class="row"><span class="label">Anaphylaxis</span><span class="yes-word">Yes</span><span class="box"></span><span class="no-word">No</span><span class="box"></span></div>
    <div class="row"><span class="label">Auto-immune disease</span><span class="yes-word">Yes</span><span class="box"></span><span class="no-word">No</span><span class="box"></span></div>
    <div class="row"><span class="label">Coeliac</span><span class="yes-word">Yes</span><span class="box"></span><span class="no-word">No</span><span class="box"></span></div>
    <div class="row"><span class="label">Depression</span><span class="yes-word">Yes</span><span class="box"></span><span class="no-word">No</span><span class="box"></span></div>
    <div class="row"><span class="label">Diabetes</span><span class="yes-word">Yes</span><span class="box"></span><span class="no-word">No</span><span class="box"></span></div>
    <div class="row"><span class="label">Epilepsy</span><span class="yes-word">Yes</span><span class="box"></span><span class="no-word">No</span><span class="box"></span></div>
    <div class="row"><span class="label">Kidney Disease</span><span class="yes-word">Yes</span><span class="box"></span><span class="no-word">No</span><span class="box"></span></div>
    <div class="row"><span class="label">Liver Disease</span><span class="yes-word">Yes</span><span class="box"></span><span class="no-word">No</span><span class="box"></span></div>
    <div class="row"><span class="label">Osteoporosis</span><span class="yes-word">Yes</span><span class="box"></span><span class="no-word">No</span><span class="box"></span></div>
    <div class="row"><span class="label">Parkinson's</span><span class="yes-word">Yes</span><span class="box"></span><span class="no-word">No</span><span class="box"></span></div>
    <div class="row"><span class="label">Radiation to Head/Neck</span><span class="yes-word">Yes</span><span class="box"></span><span class="no-word">No</span><span class="box"></span></div>
    <div class="row"><span class="label">Schizophrenia</span><span class="yes-word">Yes</span><span class="box"></span><span class="no-word">No</span><span class="box"></span></div>
    <div class="row"><span class="label">Snoring</span><span class="yes-word">Yes</span><span class="box"></span><span class="no-word">No</span><span class="box"></span></div>
    <div class="row"><span class="label">Sleep apnea</span><span class="yes-word">Yes</span><span class="box"></span><span class="no-word">No</span><span class="box"></span></div>
    <div class="row"><span class="label">Stroke</span><span class="yes-word">Yes</span><span class="box"></span><span class="no-word">No</span><span class="box"></span></div>
  </section>

  <h2 class="abs section-head" style="left:458px;top:889px">OTHER</h2>
  <div class="abs field" style="left:459px;top:908px;width:331px;height:23px"></div>
  <div class="abs field" style="left:459px;top:940px;width:331px;height:23px"></div>

  <div class="abs field" style="left:459px;top:989px;width:331px;height:70px"><p class="field-label">SIGNATURE</p></div>
  <div class="abs field" style="left:459px;top:1065px;width:331px;height:24px"><p class="field-label" style="padding:3px 6px">Date:</p></div>
</main>
</body>
</html>
```